Kestrelbrook Student Accomodation needs a business card design

Hi Guys,

We are a Student Accommodation company in Australia. We already have a logo which I will submit.

I will require the design of the business cards from you.

I am after something that looks clean, modern and that people feel interested and actually want to contact us.

We would like to see designs that are innovative.

On the business cards I will require to have:

Employee Name
Position
Phone number
Email
Facebook page

I hope you can help me with this project guys as I have heard really good things from you.

```html
<!DOCTYPE html>
<html lang="en">
<head>
<meta charset="utf-8">
<title>Kestrelbrook Student Accomodation – Business Card</title>
<link href="https://fonts.googleapis.com/css2?family=Roboto:wght@400;500;700&display=swap" rel="stylesheet">
<style>
  :root{
    --bg:#e9e9e7;
    --card:#ffffff;
    --card-shade:#f1f1f1;
    --ink:#3a3a3a;
    --ink-soft:#555555;
    --green:#2e9f1c;
    --green-dark:#1f8412;
    --gold:#f3b21c;
    --on-green:#e9f7e4;
  }
  *{margin:0;padding:0;box-sizing:border-box}
  html,body{width:1200px;height:899px;overflow:hidden}
  body{background:var(--bg);font-family:"Roboto",Arial,sans-serif;color:var(--ink)}
  .business-card{
    position:absolute;left:180px;top:210px;width:840px;height:480px;
    border-radius:34px;overflow:hidden;
    background:linear-gradient(160deg,var(--card) 45%,var(--card-shade) 100%);
    box-shadow:0 18px 40px rgba(0,0,0,.18);
  }
  .brand{
    position:absolute;left:62px;top:150px;width:270px;
    display:flex;align-items:center;gap:14px;
  }
  .brand-square{width:34px;height:34px;background:var(--gold);flex:none}
  .brand-name{
    font-weight:700;font-size:22px;line-height:1.15;text-transform:uppercase;
    color:var(--green);letter-spacing:.5px;
  }
  .contact{position:absolute;left:400px;top:82px;width:400px}
  .person-name{font-size:27px;font-weight:500;letter-spacing:1.5px;text-transform:uppercase;color:var(--ink)}
  .person-role{font-size:18px;color:var(--ink-soft);margin-top:4px}
  .address{font-size:19px;line-height:1.3;color:var(--ink);margin-top:40px}
  .channels{list-style:none;margin-top:36px}
  .channels li{display:flex;align-items:center;gap:12px;font-size:14px;color:var(--ink-soft);height:23px}
  .channels svg{width:15px;height:15px;fill:var(--ink-soft);flex:none}
  .footer-band{
    position:absolute;left:0;bottom:0;width:840px;height:62px;
    background:linear-gradient(90deg,var(--green) 0%,var(--green-dark) 100%);
  }
  .web-line{
    position:absolute;left:150px;bottom:22px;font-size:13px;letter-spacing:1px;
    color:var(--on-green);
  }
</style>
</head>
<body>
  <article class="business-card">
    <div class="brand">
      <span class="brand-square"></span>
      <span class="brand-name">Kestrelbrook Student Accomodation</span>
    </div>

    <section class="contact">
      <h1 class="person-name">Mark Ellison</h1>
      <p class="person-role">Managing Director</p>
      <p class="address">041 12th floor,Main<br>Harbour Road LKG</p>
      <ul class="channels">
        <li><svg viewBox="0 0 16 16"><path d="M4 1l3 3-2 2a9 9 0 0 0 5 5l2-2 3 3-2 3C7 15 1 9 1 3z"/></svg>012 345 6789</li>
        <li><svg viewBox="0 0 16 16"><path d="M4 0h8v16H4zM5.5 2v10h5V2zM7 13.5h2v1H7z" fill-rule="evenodd"/></svg>012 345 6789</li>
        <li><svg viewBox="0 0 16 16"><path d="M4 1h8v4H4zM1 6h14v6h-3v3H4v-3H1zM5 10v4h6v-4z" fill-rule="evenodd"/></svg>012 345 6789</li>
        <li><svg viewBox="0 0 16 16"><path d="M1 3h14v10H1zM2.5 4.5v.6L8 9l5.5-3.9v-.6z" fill-rule="evenodd"/></svg>urname@email.com</li>
        <li><svg viewBox="0 0 16 16"><path d="M8 1a7 7 0 1 0 0 14A7 7 0 0 0 8 1zm0 1.5a5.5 5.5 0 1 1 0 11 5.5 5.5 0 0 1 0-11zM2.5 7.3h11v1.4h-11zM7.3 2.5h1.4v11H7.3z" fill-rule="evenodd"/></svg>www.urwebsitename.com</li>
      </ul>
    </section>

    <div class="footer-band" role="img" aria-label="Decorative green footer band of the card"></div>
    <p class="web-line">www.urwebsitename.com</p>
  </article>
</body>
</html>
```